cryotherapy business . Whole Body Cryotherapy, Localised Cryotherapy, Cryofacials

Need home page plus services, about, pricing, online booking, contact and blog page

I want something slick, hip and professional. Our studio colours are duck egg blue, white and grey

I would also like a social media scroll at the bottom of every page

I will upload some web designs that I like the look of

Target Market(s)

Men and Women 25-45

Industry/Entity Type

Health And Wellness

Coding

Coded - Design and coding required

Number of Pages Required

5+ page

Font styles to use
Serif
Sans Serif

Requirements
Must have
• Must be eye catching and easy to navigate
Nice to have
• animation
Should not have
• Not sure what the site should not have. I am fairly open to ideas as this is a brand new business.

```html
<!DOCTYPE html>
<html lang="en">
<head>
<meta charset="utf-8">
<title>Frostline — Cryotherapy Studio</title>
<link rel="stylesheet" href="https://fonts.googleapis.com/css2?family=Montserrat:wght@400;600;700&family=Open+Sans:ital,wght@0,400;0,600;1,400&display=swap">
<style>
:root{
  --duck:#b7d8de;
  --duck-deep:#9fc8d0;
  --charcoal:#3e3c3d;
  --night:#141416;
  --grey:#a7a7a7;
  --grey-light:#e4e4e4;
  --text:#555;
  --white:#fff;
}
*{margin:0;padding:0;box-sizing:border-box}
html,body{width:1200px;height:4789px;overflow:hidden}
body{position:relative;background:var(--white);font-family:"Open Sans",sans-serif;color:var(--text)}
.abs{position:absolute}
h1,h2,h3,.brand{font-family:"Montserrat",sans-serif}
.section-title{position:absolute;left:0;width:1200px;text-align:center;font-size:40px;font-weight:700;color:#111;letter-spacing:.5px}

/* header */
.site-header{position:absolute;left:0;top:0;width:1200px;height:95px;background:var(--charcoal);z-index:3}
.brand{position:absolute;font-size:38px;font-weight:400;letter-spacing:4px;color:#cfcfcf}
.site-header .brand{left:87px;top:27px}
.main-nav{position:absolute;left:490px;top:38px;display:flex;gap:31px;font-size:17px;color:#eee}

/* hero */
.hero-photo{left:0;top:95px;width:1200px;height:650px;background:linear-gradient(180deg,#3a8fe6 0%,#6fb4ef 40%,#c7dced 75%,#e6eef5 100%)}
.hero-cut{left:0;top:660px}
.hero-title{left:88px;top:308px;font-size:54px;font-weight:700;color:#151515;letter-spacing:1px}
.hero-text{left:89px;top:394px;width:380px;font-size:18px;line-height:32px;color:#1c1c1c}
.btn{display:flex;align-items:center;justify-content:center;background:var(--duck);color:#222;font-family:"Montserrat",sans-serif}
.hero-btn{left:89px;top:530px;width:260px;height:63px;font-size:19px}

/* about */
.about-title{left:89px;top:832px;font-size:40px;font-weight:700;color:#111}
.about-text{left:89px;top:922px;width:494px;font-size:15.5px;line-height:27px;text-align:justify;color:#666}
.about-btn{left:89px;top:1128px;width:212px;height:56px;font-size:18px}
.about-hex{left:765px;top:815px}

/* services */
.services-bg{left:0;top:1280px}
.services-title{top:1370px;color:#fff}
.service{position:absolute;top:1480px;width:320px;text-align:center;color:#fff}
.service svg{display:block;margin:0 auto}
.service h3{margin-top:45px;font-size:23px;line-height:32px;font-weight:700}
.service p{margin:20px auto 0;width:282px;font-size:15.5px;line-height:27px;text-align:justify;text-align-last:center}
.service .more{display:block;margin-top:18px;font-size:15px;font-weight:600;color:var(--duck)}

/* pricing */
.pricing-title{top:2200px}
.pricing-sub{left:220px;top:2268px;width:760px;text-align:center;font-size:16px;line-height:28px;color:#555}
.plan{position:absolute;background:#f6f6f6;box-shadow:0 2px 6px rgba(0,0,0,.2);text-align:center}
.plan-head{height:58px;display:flex;align-items:center;justify-content:center;background:var(--grey-light);font-size:22px;line-height:26px;color:var(--grey)}
.plan ul{list-style:none;text-align:left;padding:22px 0 0 26px;background:var(--white)}
.plan li{display:flex;align-items:center;gap:14px;height:52px;font-size:17px;color:#b5b5b5}
.plan-price{font-size:80px;color:var(--grey);font-family:"Open Sans",sans-serif;padding-top:24px}
.plan-price small{font-size:24px}
.plan .btn{margin:22px auto 0;width:218px;height:50px;font-size:22px;background:var(--grey);color:#fff;font-family:"Open Sans",sans-serif}
.plan--left{left:165px;top:2410px;width:259px;height:513px}
.plan--right{left:758px;top:2410px;width:258px;height:513px}
.plan--feature{left:435px;top:2384px;width:310px;height:565px}
.plan--feature .plan-head{height:86px;background:var(--duck);color:#111;font-size:25px}
.plan--feature li{color:#222}
.plan--feature .plan-price{color:var(--duck-deep);padding-top:28px}
.plan--feature .btn{background:var(--duck);color:#222;width:246px;height:64px;font-size:25px}
.plan--feature ul{padding-top:20px}

/* testimonials */
.testi-bg{left:0;top:3040px}
.testi-title{top:3148px}
.testi-box{left:162px;top:3237px;width:897px;height:226px;border:2px solid #9fb6bb}
.quote-mark{font-family:Georgia,serif;font-weight:700;font-size:52px;color:#333;line-height:1}
.testi-quote{left:226px;top:3296px;width:680px;font-size:19px;line-height:33px;font-style:italic;color:#222}
.avatar{left:217px;top:3379px;width:60px;height:60px;border-radius:50%;background:linear-gradient(#d9b89b,#a4806a)}
.testi-name{left:292px;top:3384px;font-size:19px;color:#222}
.testi-role{left:292px;top:3413px;font-size:13px;font-style:italic;color:#333}
.case-btn{left:894px;top:3394px;width:126px;height:36px;border:2px solid #444;background:#fff;border-radius:2px;font-size:13px;display:flex;align-items:center;justify-content:center;color:#222}
.dots{left:556px;top:3500px;display:flex;gap:15px}
.dots span{width:19px;height:19px;border:2px solid #222;border-radius:50%;position:relative}
.dots .on::after{content:"";position:absolute;left:4px;top:4px;width:7px;height:7px;border-radius:50%;background:#222}

/* blog */
.blog-title{top:3652px}
.card{position:absolute;background:#fff;border:2px solid #ddd;box-shadow:0 1px 4px rgba(0,0,0,.18)}
.card-photo{position:absolute}
.card h3{font-size:22px;font-weight:700;color:#111;line-height:29px;text-align:center}
.card p{font-size:14px;line-height:27px;color:#777;text-align:center}
.card .btn{font-size:14px;color:#222}
.date-tag{position:absolute;background:var(--duck);color:#222;font-size:13px;line-height:16px;padding:6px 8px}
.card--main{left:91px;top:3768px;width:498px;height:453px}
.card--side{left:602px;width:513px;height:217px}

/* footer */
.footer-bg{left:0;top:4300px}
.site-footer .brand{left:87px;top:4455px;font-size:40px;color:#d8d8d8}
.footer-about{left:87px;top:4534px;width:330px;font-size:13.5px;line-height:27px;color:#fff}
.footer-head{font-family:"Montserrat",sans-serif;font-weight:600;font-size:21px;color:#fff}
.quick-links{left:497px;top:4512px;list-style:none;font-size:13.5px;line-height:27px;color:#fff}
.contact-list{left:775px;top:4510px;list-style:none;font-size:14px;color:#fff}
.contact-list li{display:flex;align-items:center;gap:18px;height:33px}
.contact-list li.indent{padding-left:37px}
.copyright{left:0;top:4728px;width:1200px;text-align:center;font-size:15px;color:#fff}
</style>
</head>
<body>

<header class="site-header">
  <div class="brand">FROSTLINE</div>
  <nav class="main-nav">
    <span>Home</span><span>Services</span><span>About</span><span>Pricing</span><span>Online Booking</span><span>Contact</span><span>Blog</span>
  </nav>
</header>

<section class="hero">
  <div class="abs hero-photo" role="img" aria-label="Client relaxing with eyes closed inside a cryotherapy chamber lit in blue"></div>
  <svg class="abs hero-cut" width="1200" height="100" viewBox="0 0 1200 100">
    <polygon points="0,18 855,88 1200,18 1200,100 0,100" fill="#fff"/>
    <polyline points="0,18 855,88 1200,18" fill="none" stroke="#b7d8de" stroke-width="5"/>
  </svg>
  <h1 class="abs hero-title">FROSTLINE</h1>
  <p class="abs hero-text">Lorem ipsum dolor sit amet, consectetur adipiscing elit. Suspendisse sed velit nisi. Ut vitae accumsan dolor.</p>
  <div class="abs btn hero-btn">MAKE AN APPOINTMENT</div>
</section>

<section class="about">
  <h2 class="abs about-title">ABOUT US</h2>
  <p class="abs about-text">Originally invented by doctors as a powerful anti-inflammatory tool, cryotherapy is a quick, noninvasive process that exposes your body to extreme cold of up to -250°F. This sudden drop in temperature increases circulation and pumps reoxygenated and nutrient enriched blood back into the bloodstream reducing pain &amp; inflammation and alleviating sore muscles.</p>
  <div class="abs btn about-btn">READ MORE</div>
  <svg class="abs about-hex" width="350" height="400" viewBox="-175 -200 350 400" role="img" aria-label="Client receiving a cryo facial treatment with cold vapour">
    <defs><linearGradient id="aboutFill" x1="0" y1="0" x2="1" y2="1"><stop offset="0" stop-color="#dfe6ee"/><stop offset=".5" stop-color="#6d8fc7"/><stop offset="1" stop-color="#2b4f98"/></linearGradient></defs>
    <polygon points="0,-197 170,-98 170,98 0,197 -170,98 -170,-98" fill="url(#aboutFill)" stroke="#e8e8e8" stroke-width="4"/>
  </svg>
</section>

<section class="services">
  <svg class="abs services-bg" width="1200" height="834" viewBox="0 0 1200 834" role="img" aria-label="Dark studio backdrop with cryotherapy chamber">
    <defs><linearGradient id="svcFill" x1="0" y1="0" x2="0" y2="1"><stop offset="0" stop-color="#0b0b0e"/><stop offset=".7" stop-color="#1b1b20"/><stop offset="1" stop-color="#2c2c30"/></linearGradient></defs>
    <polygon points="0,113 344,6 1200,113 1200,834 0,834" fill="url(#svcFill)"/>
    <polyline points="0,110 344,3 1200,110" fill="none" stroke="#b7d8de" stroke-width="5"/>
  </svg>
  <h2 class="section-title services-title">SERVICES</h2>

  <div class="service" style="left:70px">
    <svg width="300" height="300" viewBox="-150 -150 300 300" role="img" aria-label="Smiling client wrapped in a towel inside a whole body cryo chamber"><polygon points="0,-142 123,-71 123,71 0,142 -123,71 -123,-71" fill="#7e9ed8"/></svg>
    <h3>Whole Body<br>Cryotherapy</h3>
    <p>Whole Body Cryotherapy is a quick, non-invasive process that exposes your body to extreme cold up to -250F.</p>
    <span class="more">Read More &gt;&gt;</span>
  </div>
  <div class="service" style="left:431px">
    <svg width="300" height="300" viewBox="-150 -150 300 300" role="img" aria-label="Client lying down while cold vapour is applied to the face"><polygon points="0,-150 130,-75 130,75 0,150 -130,75 -130,-75" fill="#5f80b5"/></svg>
    <h3>Local<br>Cryotherapy</h3>
    <p>Local cryotherapy acts as a higher intensity, more efficient form of “icing.” With the use of liquid nitrogen, the treatment .</p>
    <span class="more">Read More &gt;&gt;</span>
  </div>
  <div class="service" style="left:810px">
    <svg width="300" height="300" viewBox="-150 -150 300 300" role="img" aria-label="Woman holding an ice cube against her cheek"><polygon points="0,-142 123,-71 123,71 0,142 -123,71 -123,-71" fill="#e9d6cb"/></svg>
    <h3>Cryo<br>Facial</h3>
    <p>Cryo Facials apply pressurized liquid nitrogen vapors to the face, neck and scalp to help stimulate and improve .</p>
    <span class="more">Read More &gt;&gt;</span>
  </div>
</section>

<section class="pricing">
  <h2 class="section-title pricing-title">PRICING</h2>
  <p class="abs pricing-sub">Our Monthly Membership allows you unlimited cryo for an entire month (up to 1 session of any cryo treatment/day). Imagine relief &amp; rejuvenation every day.</p>

  <div class="plan plan--left">
    <div class="plan-head">Whole Body<br>Cryotherapy</div>
    <ul>
      <li><svg width="26" height="20" viewBox="0 0 26 20"><path d="M2 10l8 8L24 3" fill="none" stroke="#d4d4d4" stroke-width="3"/></svg>Single</li>
      <li><svg width="26" height="20" viewBox="0 0 26 20"><path d="M2 10l8 8L24 3" fill="none" stroke="#d4d4d4" stroke-width="3"/></svg>10 Pack</li>
      <li><svg width="26" height="20" viewBox="0 0 26 20"><path d="M2 10l8 8L24 3" fill="none" stroke="#d4d4d4" stroke-width="3"/></svg>20 Pack</li>
      <li><svg width="26" height="20" viewBox="0 0 26 20"><path d="M2 10l8 8L24 3" fill="none" stroke="#d4d4d4" stroke-width="3"/></svg>Monthly</li>
    </ul>
    <div class="plan-price">$400<small>/mo.</small></div>
    <div class="btn">Book A Session</div>
  </div>

  <div class="plan plan--feature">
    <div class="plan-head">★&nbsp; Local Cryotherapy</div>
    <ul>
      <li><svg width="26" height="20" viewBox="0 0 26 20"><path d="M2 10l8 8L24 3" fill="none" stroke="#b7d8de" stroke-width="3"/></svg>Single</li>
      <li><svg width="26" height="20" viewBox="0 0 26 20"><path d="M2 10l8 8L24 3" fill="none" stroke="#b7d8de" stroke-width="3"/></svg>10 Pack</li>
      <li><svg width="26" height="20" viewBox="0 0 26 20"><path d="M2 10l8 8L24 3" fill="none" stroke="#b7d8de" stroke-width="3"/></svg>20 Pack</li>
      <li><svg width="26" height="20" viewBox="0 0 26 20"><path d="M2 10l8 8L24 3" fill="none" stroke="#b7d8de" stroke-width="3"/></svg>Monthly*</li>
    </ul>
    <div class="plan-price">$400<small>/mo.</small></div>
    <div class="btn">Book A Session</div>
  </div>

  <div class="plan plan--right">
    <div class="plan-head">Cryo Facial</div>
    <ul>
      <li><svg width="26" height="20" viewBox="0 0 26 20"><path d="M2 10l8 8L24 3" fill="none" stroke="#d4d4d4" stroke-width="3"/></svg>Single</li>
      <li><svg width="26" height="20" viewBox="0 0 26 20"><path d="M2 10l8 8L24 3" fill="none" stroke="#d4d4d4" stroke-width="3"/></svg>10 Pack</li>
      <li><svg width="26" height="20" viewBox="0 0 26 20"><path d="M2 10l8 8L24 3" fill="none" stroke="#d4d4d4" stroke-width="3"/></svg>20 Pack</li>
      <li><svg width="26" height="20" viewBox="0 0 26 20"><path d="M2 10l8 8L24 3" fill="none" stroke="#d4d4d4" stroke-width="3"/></svg>Monthly*</li>
    </ul>
    <div class="plan-price">$400<small>/mo.</small></div>
    <div class="btn">Book A Session</div>
  </div>
</section>

<section class="testimonials">
  <svg class="abs testi-bg" width="1200" height="540" viewBox="0 0 1200 540">
    <polygon points="0,76 858,7 1200,76 1200,538 0,538" fill="#bcdbe2"/>
    <polyline points="0,76 858,7 1200,76" fill="none" stroke="#111" stroke-width="5"/>
  </svg>
  <h2 class="section-title testi-title">TESTIMONALS</h2>
  <div class="abs testi-box"></div>
  <span class="abs quote-mark" style="left:198px;top:3282px">“</span>
  <p class="abs testi-quote">Fantastic communication and very professional experience - I have sent two people along to try it as it works great !</p>
  <span class="abs quote-mark" style="left:578px;top:3333px">”</span>
  <div class="abs avatar" role="img" aria-label="Client portrait"></div>
  <span class="abs testi-name">Daniel</span>
  <span class="abs testi-role">Clients</span>
  <div class="abs case-btn">Read Case Study</div>
  <div class="abs dots"><span></span><span class="on"></span><span></span></div>
</section>

<section class="blog">
  <h2 class="section-title blog-title">OUR BLOG</h2>

  <article class="card card--main">
    <div class="card-photo" style="left:0;top:0;width:494px;height:227px;background:linear-gradient(135deg,#e9dcd2,#c7b9b3 50%,#8fc7e3)" role="img" aria-label="Feet resting on a glowing cryo treatment platform"></div>
    <span class="date-tag" style="left:0;top:196px">▦ August 22, 2013</span>
    <h3 class="abs" style="left:0;top:250px;width:494px">LOREM IPSUM DOLOR SIT AMET</h3>
    <p class="abs" style="left:52px;top:296px;width:390px">Lorem ipsum dolor sit amet, consectetur adipiscing elit. Suspendisse sed velit nisi. Ut vitae accumsan dolor, id porttitor enim. Phasellus consequat tellus nec lectus</p>
    <div class="abs btn" style="left:192px;top:394px;width:129px;height:41px">READ MORE</div>
  </article>

  <article class="card card--side" style="top:3768px">
    <div class="card-photo" style="left:0;top:0;width:197px;height:213px;background:linear-gradient(135deg,#f3f3f3,#e3c3b0)" role="img" aria-label="Client receiving localised cryotherapy on the back"></div>
    <span class="date-tag" style="left:0;top:0">JULY 24,<br>2012</span>
    <h3 class="abs" style="left:215px;top:30px;width:280px">LOREM IPSUM DOLOR<br>SIT AMET</h3>
    <p class="abs" style="left:210px;top:88px;width:290px">Lorem ipsum dolor sit amet, consectetur adipiscing elit. Suspendisse sed velit nisi. Ut vitae accumsan dolor, id porttitor</p>
    <div class="abs btn" style="left:295px;top:178px;width:120px;height:33px">READ MORE</div>
  </article>

  <article class="card card--side" style="top:4004px">
    <div class="card-photo" style="left:0;top:0;width:197px;height:213px;background:linear-gradient(135deg,#e8f0f6,#d9c7bc)" role="img" aria-label="Woman with cold vapour around her face"></div>
    <span class="date-tag" style="left:0;top:0">February<br>3, 2009</span>
    <h3 class="abs" style="left:210px;top:30px;width:280px">LOREM IPSUM DOLOR<br>SIT AMET</h3>
    <p class="abs" style="left:210px;top:88px;width:290px">Lorem ipsum dolor sit amet, consectetur adipiscing elit. Suspendisse sed velit nisi. Ut vitae accumsan dolor, id porttitor</p>
    <div class="abs btn" style="left:295px;top:174px;width:115px;height:35px">READ MORE</div>
  </article>
</section>

<footer class="site-footer">
  <svg class="abs footer-bg" width="1200" height="489" viewBox="0 0 1200 489">
    <polygon points="0,100 344,8 1200,100 1200,489 0,489" fill="#4a4849"/>
    <polyline points="0,100 344,8 1200,100" fill="none" stroke="#b7d8de" stroke-width="6"/>
  </svg>
  <div class="brand">FROSTLINE</div>
  <p class="abs footer-about">Originally invented by doctors as a powerful anti-inflammatory tool, cryotherapy is a quick, noninvasive process that exposes your body to extreme cold</p>
  <h3 class="abs footer-head" style="left:497px;top:4444px">Quick Links</h3>
  <ul class="abs quick-links">
    <li>Home</li><li>Services</li><li>About</li><li>Pricing</li><li>Online Booking</li><li>Contact</li><li>Blog</li>
  </ul>
  <h3 class="abs footer-head" style="left:775px;top:4444px">Contact Us</h3>
  <ul class="abs contact-list">
    <li><svg width="18" height="20" viewBox="0 0 18 20"><path d="M9 1a6 6 0 0 0-6 6c0 5 6 12 6 12s6-7 6-12a6 6 0 0 0-6-6z" fill="#fff"/><circle cx="9" cy="7" r="2.2" fill="#4a4849"/></svg>48 Harbour Lane</li>
    <li class="indent">3000 Seaview, Victoria</li>
    <li><svg width="18" height="18" viewBox="0 0 18 18"><path d="M4 1l3 4-2 2c1 2 3 4 5 5l2-2 4 3-2 3C8 16 2 10 1 4z" fill="#fff"/></svg>+61 400 000 123</li>
    <li><svg width="18" height="14" viewBox="0 0 18 14"><rect x="1" y="1" width="16" height="12" fill="#fff"/><path d="M1 1l8 7 8-7" fill="none" stroke="#4a4849" stroke-width="1.5"/></svg>info@frostlinestudio.com.au</li>
  </ul>
  <p class="abs copyright">Copyright © 2019 Frostlinestudio. All Rights Reserved</p>
</footer>

</body>
</html>
```